Brenwick Structures Construction Company Seeking Modern Website

We are a small construction company wanting to create a web presence. We don't have much in the way of current content but will get photos as they come in. Attached is a picture of our business card.
The pages we would like on the menu are:
Home
Portfolio
Product Specs
Testimonials
Our Process
Contact
Some designs we like are:
http://www.tovasheds-example.com/
http://www.qrnstructures-example.com/
http://dunholtbarns-example.com/
http://pellingframes-example.com/
Not much requirements other than that so feel free to be creative!
Updates
Target Market(s)
Construction
Commercial and Residential Buildings
Industry/Entity Type
Construction Company
Number of Pages Required
5+ page
Look and feel

```html
<!DOCTYPE html>
<html lang="en">
<head>
<meta charset="utf-8">
<title>Brenwick Structures — Home</title>
<link href="https://fonts.googleapis.com/css2?family=Open+Sans:wght@400;600;700&display=swap" rel="stylesheet">
<style>
:root{
  --blue:#0d9bd8;
  --blue-btn:#1aa3e0;
  --red:#d42f25;
  --red-deep:#a50f12;
  --ink:#2b2b2b;
  --muted:#555;
  --panel:#f3f3f3;
  --dark:#232323;
  --footer-text:#d8d8d8;
  --white:#fff;
}
*{box-sizing:border-box;margin:0;padding:0}
html,body{width:730px;height:1200px;overflow:hidden}
body{position:relative;font-family:"Open Sans",Arial,sans-serif;color:var(--ink);
  background:linear-gradient(#fff 0,#fdf6f4 300px,#f9e6e3 348px,var(--blue) 348px,var(--blue) 100%)}
.abs{position:absolute}
.brand{left:59px;top:12px;font-size:25px;font-weight:700;color:var(--blue);letter-spacing:-.3px}
.tagline{left:58px;top:48px;font-size:8px;color:#333}
.call{right:62px;top:13px;font-size:8px;color:#333;display:flex;align-items:center;gap:4px}
.call b{color:var(--red);font-weight:600}
.nav{right:59px;top:42px;display:flex;gap:21px;font-size:8px;color:#333;align-items:center}
.nav .active{background:var(--red);color:#fff;border:1.5px solid #8c1410;border-radius:12px;padding:3px 10px}
.hero{left:59px;top:70px;width:611px;height:278px;background:linear-gradient(135deg,#dcdcdc 0,#f4f4f4 40%,#e8e8e8 70%,#cfd2d4 100%)}
.hero-arrow{top:207px;width:18px;height:18px;border-radius:50%;background:rgba(120,120,120,.55)}
.cta{left:59px;top:348px;width:611px;height:65px;background:var(--red)}
.cta p{position:absolute;left:19px;top:21px;width:420px;font-size:9px;font-weight:600;color:#fff;line-height:13px}
.quote-btn{position:absolute;left:481px;top:21px;width:115px;height:23px;border-radius:12px;background:var(--blue-btn);
  border:1.5px solid #0b78ab;color:#fff;font-size:8.5px;font-weight:600;display:flex;align-items:center;justify-content:center}
.main{left:59px;top:413px;width:611px;height:449px;background:#fff}
.welcome h2{position:absolute;left:0;width:611px;top:18px;text-align:center;font-size:15px;font-weight:600;letter-spacing:.5px}
.welcome p{position:absolute;left:9px;width:594px;top:47px;text-align:center;font-size:7px;line-height:12.4px;color:var(--muted)}
.service{top:99px;width:291px;height:70px;background:var(--panel)}
.service .icon{position:absolute;left:8px;top:6px;width:71px;height:57px;background:#fff;display:flex;align-items:center;justify-content:center}
.service h3{position:absolute;left:92px;top:5px;font-size:10.5px;font-weight:400;color:#333}
.service p{position:absolute;left:92px;top:22px;width:190px;font-size:7px;line-height:10.5px;color:var(--muted)}
.service a{position:absolute;left:92px;top:50px;font-size:6.5px;color:var(--red);text-decoration:underline;display:flex;align-items:center;gap:3px}
.portfolio-title{left:8px;top:214px;font-size:15.5px;font-weight:600;letter-spacing:.3px}
.pf-nav{right:8px;top:216px}
.card{top:241px;width:140px;height:156px;border:1px solid #e4e4e4;background:#fff}
.card .photo{height:108px}
.card h4{position:absolute;left:9px;top:116px;font-size:8px;font-weight:400;color:#333}
.card p{position:absolute;left:9px;top:131px;font-size:6.2px;color:#666;display:flex;gap:8px;align-items:center}
.testimonials{left:59px;top:862px;width:611px;height:228px;background:radial-gradient(ellipse at 50% 40%,#b4141a 0,var(--red-deep) 70%,#8d0c0f 100%)}
.testimonials h2{position:absolute;width:100%;top:23px;text-align:center;color:#fff;font-size:15px;font-weight:600;letter-spacing:.5px}
.avatar{left:273px;top:53px;width:65px;height:65px;border-radius:50%;border:3px solid #fff;background:linear-gradient(#b9c0c6,#6d747b)}
.testimonials blockquote{position:absolute;left:120px;width:371px;top:134px;text-align:center;color:#fff;font-size:8.3px;line-height:14px}
.testimonials cite{position:absolute;width:100%;top:190px;text-align:center;color:#fff;font-size:7.3px;font-weight:700;font-style:normal}
.t-arrow{top:152px;width:25px;height:25px;border:1px solid #fff;border-radius:50%;display:flex;align-items:center;justify-content:center}
.footer{left:59px;top:1090px;width:611px;height:110px;background:var(--dark)}
.fnav{position:absolute;left:9px;top:21px;display:flex;align-items:center;font-size:7px;color:var(--footer-text)}
.fnav span{padding:0 8px;border-left:1px solid #888;line-height:8px}
.fnav span.first{border:1px solid #ccc;border-radius:10px;padding:4px 9px;margin-right:2px;line-height:normal}
.fnav span.first + span{border-left:none}
.social{position:absolute;left:541px;top:24px;display:flex;gap:10px}
.social i{display:block;width:9px;height:9px;border-radius:50%;background:#e6e6e6}
.tip{position:absolute;left:541px;top:40px;width:40px;height:13px;border-radius:7px;background:var(--blue-btn)}
.contacts{position:absolute;left:9px;top:72px;width:594px;display:flex;align-items:flex-start;font-size:6px;color:var(--footer-text);line-height:9px}
.contacts .item{display:flex;gap:6px;align-items:flex-start;margin-right:26px}
.contacts .copy{margin-left:auto}
.dot{width:12px;height:12px;border-radius:50%;background:#fff;display:flex;align-items:center;justify-content:center;flex:none}
</style>
</head>
<body>
<div class="abs brand">Brenwick Structures</div>
<div class="abs tagline">Building Dreams, So You Can Build Memories</div>
<div class="abs call">
  <svg width="8" height="10" viewBox="0 0 8 10"><path d="M2 0 L3.5 2.5 L2.5 3.5 Q3 6 5 7.5 L6 6.5 L8 8.2 L6.6 9.8 Q1.5 8.5 0.3 1.6 Z" fill="#d42f25"/></svg>
  <b>CALL US TODAY!</b> 555.014.2270
</div>
<nav class="abs nav">
  <span class="active">Home</span><span>Portfolio</span><span>Product Specs</span><span>Testimonials</span><span>Our Process</span><span>Contact</span>
</nav>

<div class="abs hero" role="img" aria-label="Overhead photo of a builder in a hard hat drafting blueprints beside safety tools"></div>
<div class="abs hero-arrow" style="left:74px"><svg width="18" height="18"><path d="M10.5 5 L6.5 9 L10.5 13" stroke="#fff" stroke-width="1.6" fill="none"/></svg></div>
<div class="abs hero-arrow" style="left:637px"><svg width="18" height="18"><path d="M7.5 5 L11.5 9 L7.5 13" stroke="#fff" stroke-width="1.6" fill="none"/></svg></div>

<section class="abs cta">
  <p>Lorem ipsum dolor sit amet, consectetur adipiscing elit. Aliquam accumsan faucibus eros, quis volutpat sem.</p>
  <div class="quote-btn">GET A QUOTE</div>
</section>

<main class="abs main">
  <div class="welcome">
    <h2>WELCOME</h2>
    <p>Lorem ipsum dolor sit amet, consectetur adipiscing elit. Pellentesque nec tempor nibh. Nullam eget leo finibus, dictum mauris in, congue mi. Morbi sed iaculis nibh, viverra eleifend mauris. In ornare rutrum libero ut scelerisque. Aliquam ut augue eleifend massa molestie efficitur. Sed odio lorem, ullamcorper quis lorem in, tincidunt ullamcorper mauris. Donec vitae ornare arcu. Nunc vitae sapien ultricies, fermentum odio in, tempus ex. Nullam a interdum lacus.</p>
  </div>

  <div class="abs service" style="left:8px">
    <div class="icon"><svg width="44" height="22" viewBox="0 0 44 22" fill="none" stroke="#555" stroke-width="1.2"><rect x="1" y="8" width="9" height="13"/><rect x="14" y="2" width="14" height="19"/><rect x="32" y="8" width="10" height="13"/><path d="M3 11h2M6 11h2M3 14h2M6 14h2M3 17h2M6 17h2M17 5h3M22 5h3M17 9h3M22 9h3M17 13h3M22 13h3M34 11h2M38 11h2M34 14h2M38 14h2M34 17h2M38 17h2M19 21v-4h4v4"/></svg></div>
    <h3>Commercial Construction</h3>
    <p>Vestibulum sed lectus viverra, vulputate quam sit amet, rutrum dui. Cras</p>
    <a>Read More <svg width="7" height="7"><circle cx="3.5" cy="3.5" r="3.5" fill="#d42f25"/><path d="M2.8 2 L4.3 3.5 L2.8 5" stroke="#fff" stroke-width="1" fill="none"/></svg></a>
  </div>
  <div class="abs service" style="left:312px">
    <div class="icon"><svg width="26" height="22" viewBox="0 0 26 22"><path d="M13 1 L25 12 L22 12 L22 21 L16 21 L16 14 L10 14 L10 21 L4 21 L4 12 L1 12 Z" fill="#555"/></svg></div>
    <h3>Residential Buildings</h3>
    <p>Vestibulum sed lectus viverra, vulputate quam sit amet, rutrum dui. Cras</p>
    <a>Read More <svg width="7" height="7"><circle cx="3.5" cy="3.5" r="3.5" fill="#d42f25"/><path d="M2.8 2 L4.3 3.5 L2.8 5" stroke="#fff" stroke-width="1" fill="none"/></svg></a>
  </div>

  <h2 class="abs portfolio-title">PORTFOLIO</h2>
  <svg class="abs pf-nav" width="18" height="12" viewBox="0 0 18 12"><path d="M6 1 L1.5 6 L6 11" stroke="#c4161c" stroke-width="2" fill="none"/><path d="M12 1 L16.5 6 L12 11" stroke="#555" stroke-width="1.6" fill="none"/></svg>

  <div class="abs card" style="left:8px">
    <div class="photo" role="img" aria-label="Steel frame building under construction with a crane against a blue sky" style="background:linear-gradient(160deg,#1c4f9a,#5d8fd0 50%,#23282f)"></div>
    <h4>Lorem ipsum dolor sit amet,</h4>
    <p><svg width="6" height="8" viewBox="0 0 6 8"><path d="M3 8 L0.6 4.2 A3 3 0 1 1 5.4 4.2 Z" fill="#999"/></svg>consectetur adipiscing elit.</p>
  </div>
  <div class="abs card" style="left:160px">
    <div class="photo" role="img" aria-label="Two workers in yellow hard hats building a wooden form" style="background:linear-gradient(160deg,#8a6d4f,#c9a177 50%,#5a4a3c)"></div>
    <h4>Lorem ipsum dolor sit amet,</h4>
    <p><svg width="6" height="8" viewBox="0 0 6 8"><path d="M3 8 L0.6 4.2 A3 3 0 1 1 5.4 4.2 Z" fill="#999"/></svg>consectetur adipiscing elit.</p>
  </div>
  <div class="abs card" style="left:311px">
    <div class="photo" role="img" aria-label="Excavator bucket digging earth at sunrise" style="background:linear-gradient(160deg,#3a4d66,#9aa8b7 45%,#dcc28a 60%,#2d3644)"></div>
    <h4>Lorem ipsum dolor sit amet,</h4>
    <p><svg width="6" height="8" viewBox="0 0 6 8"><path d="M3 8 L0.6 4.2 A3 3 0 1 1 5.4 4.2 Z" fill="#999"/></svg>consectetur adipiscing elit.</p>
  </div>
  <div class="abs card" style="left:463px">
    <div class="photo" role="img" aria-label="Workers on scaffolding among rebar columns" style="background:linear-gradient(160deg,#6d5f55,#a79a8d 50%,#4a3f3a)"></div>
    <h4>Lorem ipsum dolor sit amet,</h4>
    <p><svg width="6" height="8" viewBox="0 0 6 8"><path d="M3 8 L0.6 4.2 A3 3 0 1 1 5.4 4.2 Z" fill="#999"/></svg>consectetur adipiscing elit.</p>
  </div>
</main>

<section class="abs testimonials">
  <h2>CLIENT TESTIMONIALS</h2>
  <div class="abs avatar" role="img" aria-label="Client portrait"></div>
  <div class="abs t-arrow" style="left:49px"><svg width="8" height="8"><path d="M5 1 L2 4 L5 7" stroke="#fff" stroke-width="1.2" fill="none"/></svg></div>
  <div class="abs t-arrow" style="left:537px"><svg width="8" height="8"><path d="M3 1 L6 4 L3 7" stroke="#fff" stroke-width="1.2" fill="none"/></svg></div>
  <blockquote>Lorem ipsum dolor sit amet, consectetur adipiscing elit. Vestibulum egetvel lacus pretium rhoncus a quis nisly Ut vehicula gravida dui in pulvinar donec diam elit consequat eget augue vitae aliquet sollicitudin.</blockquote>
  <cite>Owen Carlisle</cite>
</section>

<footer class="abs footer">
  <div class="fnav"><span class="first">Home</span><span>Portfolio</span><span>Product Specs</span><span>Testimonials</span><span>Our Process</span><span>Contact</span></div>
  <div class="social"><i></i><i></i><i></i><i></i></div>
  <div class="tip"></div>
  <div class="contacts">
    <div class="item"><span class="dot"><svg width="6" height="8" viewBox="0 0 6 8"><path d="M3 8 L0.6 4.2 A3 3 0 1 1 5.4 4.2 Z" fill="#232323"/></svg></span><span>48 Harlow Lane, Brookvale, Kenmore County<br>50219, Riverside District</span></div>
    <div class="item"><span class="dot"><svg width="7" height="7" viewBox="0 0 8 10"><path d="M2 0 L3.5 2.5 L2.5 3.5 Q3 6 5 7.5 L6 6.5 L8 8.2 L6.6 9.8 Q1.5 8.5 0.3 1.6 Z" fill="#232323"/></svg></span><span style="padding-top:2px">+1 555 019 4836</span></div>
    <div class="item"><span class="dot"><svg width="7" height="5" viewBox="0 0 7 5"><rect width="7" height="5" fill="#232323"/><path d="M0 0 L3.5 2.8 L7 0" stroke="#fff" stroke-width=".7" fill="none"/></svg></span><span style="padding-top:2px">info@brenwick-example.com</span></div>
    <div class="copy" style="padding-top:2px">©Copyright 2015 brenwick-example. All Rights Reserved.</div>
  </div>
</footer>
</body>
</html>
```